Business Card Design

New business card design

Target Market(s)

Residential & Commercial Property Managers

Industry/Entity Type

Plumbing Services

Contact Information for Business Card

Name - Rowan Keddle, title - Director, Phone Number - 0431 286 517, email - rowan@tbk-plumbing.com.au, Company ABN - 73 215 904 386,

Font styles to use
Sans Serif

Colors
0054AA
0677BA
7BADD7
CADEEF
E8F1F8

```html
<!DOCTYPE html>
<html lang="en">
<head>
<meta charset="utf-8">
<title>TBK Plumbing Services – Business Card</title>
<link href="https://fonts.googleapis.com/css2?family=Open+Sans:wght@400;600;700&display=swap" rel="stylesheet">
<style>
  :root {
    --deep-blue: #0054AA;
    --brand-blue: #0677BA;
    --sky-blue: #29A9E0;
    --soft-blue: #7BADD7;
    --pale-blue: #CADEEF;
    --mist-blue: #E8F1F8;
    --ink: #1E2328;
    --paper: #FFFFFF;
    --backdrop: #2A2D31;
  }
  * { box-sizing: border-box; margin: 0; padding: 0; }
  html, body {
    width: 1200px; height: 900px; overflow: hidden;
    background: var(--backdrop);
    font-family: "Open Sans", Arial, sans-serif;
  }
  .canvas {
    position: relative; width: 1200px; height: 900px;
    display: flex; align-items: center; justify-content: center; gap: 60px;
  }
  .card {
    position: relative; width: 520px; height: 300px;
    border-radius: 4px; box-shadow: 0 14px 34px rgba(0,0,0,.45);
    overflow: hidden;
  }
  .card-front { background: var(--paper); color: var(--ink); }
  .card-back {
    background: linear-gradient(135deg, var(--sky-blue), var(--brand-blue));
    display: flex; align-items: center; justify-content: center;
  }
  .wordmark { text-align: center; font-weight: 600; line-height: 1; }
  .wordmark-name { font-size: 58px; letter-spacing: 6px; }
  .wordmark-tagline { font-size: 11px; letter-spacing: 7px; margin-top: 10px; text-transform: lowercase; }
  .card-back .wordmark { color: var(--paper); }
  .card-front .wordmark { position: absolute; right: 40px; top: 34px; color: var(--ink); }
  .card-front .wordmark-name { font-size: 46px; }
  .card-front .wordmark-tagline { font-size: 9px; color: #6B6F73; }
  .holder { position: absolute; left: 30px; top: 128px; }
  .holder-name { color: var(--sky-blue); font-weight: 700; font-size: 21px; }
  .holder-title { font-size: 13px; color: #444; margin-top: 2px; }
  .divider {
    position: absolute; left: 30px; right: 30px; top: 190px;
    height: 1px; background: var(--sky-blue);
  }
  .abn { position: absolute; right: 30px; top: 162px; font-size: 15px; }
  .abn-label { color: var(--sky-blue); }
  .contacts { position: absolute; left: 30px; top: 204px; list-style: none; font-size: 13px; }
  .contacts li { display: flex; align-items: center; gap: 8px; margin-bottom: 6px; }
  .contacts svg { width: 12px; height: 12px; fill: var(--sky-blue); }
</style>
</head>
<body>
<main class="canvas">
  <section class="card card-front" aria-label="Card front">
    <div class="wordmark">
      <div class="wordmark-name">tbk</div>
      <div class="wordmark-tagline">plumbing services</div>
    </div>
    <div class="holder">
      <div class="holder-name">Rowan Keddle</div>
      <div class="holder-title">Director</div>
    </div>
    <div class="abn"><span class="abn-label">ABN</span> - 73 215 904 386</div>
    <div class="divider"></div>
    <ul class="contacts">
      <li>
        <svg viewBox="0 0 24 24" aria-hidden="true"><path d="M6.6 10.8a15 15 0 0 0 6.6 6.6l2.2-2.2c.3-.3.7-.4 1-.2 1.1.4 2.3.6 3.6.6.6 0 1 .4 1 1V20c0 .6-.4 1-1 1A17 17 0 0 1 3 4c0-.6.4-1 1-1h3.5c.6 0 1 .4 1 1 0 1.3.2 2.5.6 3.6.1.3 0 .7-.2 1z"/></svg>
        0431 286 517
      </li>
      <li>
        <svg viewBox="0 0 24 24" aria-hidden="true"><path d="M2 5h20v14H2zm2 2v.5l8 5 8-5V7l-8 5z"/></svg>
        rowan@tbk-plumbing.com.au
      </li>
    </ul>
  </section>
  <section class="card card-back" aria-label="Card back">
    <div class="wordmark">
      <div class="wordmark-name">tbk</div>
      <div class="wordmark-tagline">plumbing services</div>
    </div>
  </section>
</main>
</body>
</html>
```